Website Design for Chef Wen Chinese Restaurant

Chef Wen is a new Chinese Restaurant. It offers exceptional dining experience with authentic and dynamic dishes created with quality ingredients.

A vivid website theme is required to promote this new restaurant online. Logo, menu, wine list and a few other files are attached for help with designing.

A very rough demo website has been setup and can be accessed via http://www.chefwen.com.au. It is for telling designers what content is shown up on each page (except for homepage). By reading the about us page, designers can get some more info of Chef Wen. However, the layout, theme color, font, etc are not set in stone. Visitors should be able to feel Chef Wen restaurant's authentic Chinese cuisine and high hygiene standard. Home page of the website could be The "Our website is coming soon" description is shown on demo site but do not required to be presented on new design.

Some main pages design should be included: Home (landing page), About us, Menu (Dishes), Winelist, Gallery, Contact us. No HTML and coding required. The output should be well layered psd or png files with acceptable resolution for web use.

A few other website can be referred to are:

http://larkspurasian.com.au/
http://www.river-lamp.com/
http://tamworthy.com.au/
http://harbelrestaurant.com.au/
http://www.quillerestaurant.com.au/
http://www.thekiln.com.au/

Industry/Entity Type

Restaurant

Requirements
Nice to have
• I expect designs of at least these webpages: homepage, menu page and contact us page. If you can provide "about us" page as well, it will probably help you win the competition. well layered psd or png file is my preference.
Should not have
• You don't have to make html/cs/js or any coding. All I need is just art design

```html
<!DOCTYPE html>
<html lang="en">
<head>
<meta charset="utf-8">
<title>Chef Wen Chinese Restaurant</title>
<link href="https://fonts.googleapis.com/css2?family=Oswald:wght@400;500&family=Roboto:wght@300;400;500&family=Open+Sans:wght@400;600;700&display=swap" rel="stylesheet">
<style>
:root{
  --cream:#fefcc8;
  --red:#d50d0d;
  --red-dark:#a60606;
  --ink:#2b2b2b;
  --grey:#666;
  --light:#e9e9e9;
  --band:#3b3b3b;
  --footer:#050505;
  --footer-bar:#2a2a2a;
  --white:#fff;
}
*{box-sizing:border-box;margin:0;padding:0}
html,body{width:1200px;height:2426px;overflow:hidden}
body{position:relative;background:var(--white);font-family:"Open Sans",sans-serif;color:var(--ink)}
.abs{position:absolute}

/* header */
.site-header{position:absolute;left:0;top:0;width:1200px;height:197px;background:var(--cream)}
.contact-line{position:absolute;left:171px;font-family:"Roboto",sans-serif;font-size:15px;color:#333}
.brand{position:absolute;left:450px;top:30px;width:300px;text-align:center}
.brand-mark{width:34px;height:34px;background:var(--red);margin:0 auto 14px}
.brand-name{font-family:"Roboto",sans-serif;font-weight:500;font-size:17px;color:#111;letter-spacing:.5px;text-transform:uppercase}
.search{position:absolute;left:841px;top:60px;width:187px;height:39px;background:var(--white);border:1px solid #ddd;border-radius:3px;font-family:"Roboto",sans-serif;font-size:11px;color:#999;padding:12px 14px}
.search svg{position:absolute;right:12px;top:12px}

/* nav ribbon */
.ribbon-tail{position:absolute;top:170px;width:60px;height:51px;background:var(--red-dark)}
.ribbon-tail.left{left:100px;clip-path:polygon(0 0,100% 0,100% 100%,0 100%,28% 50%)}
.ribbon-tail.right{left:1040px;clip-path:polygon(0 0,100% 0,72% 50%,100% 100%,0 100%)}
.main-nav{position:absolute;left:157px;top:157px;width:886px;height:56px;background:var(--red);display:flex;justify-content:space-around;align-items:center;padding:0 20px;box-shadow:0 3px 6px rgba(0,0,0,.25)}
.main-nav a{color:var(--white);text-decoration:none;font-family:"Roboto",sans-serif;font-size:15px}

/* hero */
.hero{position:absolute;left:0;top:197px;width:1200px;height:498px;background:radial-gradient(ellipse at 40% 65%,#d9a55a 0%,#b9833d 25%,#6f8a3b 55%,#4f6e2a 80%,#3e5a22 100%)}
.hero-text{position:absolute;left:0;width:1200px;text-align:center;color:var(--white);font-family:"Oswald",sans-serif;text-shadow:0 2px 6px rgba(0,0,0,.4)}
.slider-dots{position:absolute;left:543px;top:653px;width:109px;height:42px;background:rgba(40,40,40,.75);border-radius:4px 4px 0 0;display:flex;justify-content:center;align-items:center;gap:8px}
.slider-dots span{width:11px;height:11px;border-radius:50%;background:var(--white)}
.slider-dots span.active{background:var(--red);box-shadow:0 0 0 2px #fff inset}
.hero-shadow{position:absolute;left:60px;top:695px;width:1080px;height:24px;background:radial-gradient(ellipse at 50% 0,rgba(0,0,0,.18),transparent 70%)}

/* section headings */
.section-title{position:absolute;left:0;width:1200px;text-align:center;font-family:"Roboto",sans-serif;color:#222}
.divider{position:absolute;left:280px;width:640px;height:2px;background:linear-gradient(90deg,transparent,#e2e2e2 20%,#e2e2e2 80%,transparent)}
.divider-badge{position:absolute;left:581px;width:38px;height:38px;border-radius:50%;background:var(--white);border:1px solid #ddd;display:flex;align-items:center;justify-content:center}
.intro{position:absolute;left:205px;top:845px;width:790px;text-align:center;font-size:12.5px;line-height:23px;color:#555}

/* dish cards */
.dish-photo{position:absolute;height:181px;width:272px;box-shadow:0 6px 8px -4px rgba(0,0,0,.25)}
.price-tag{position:absolute;width:68px;height:29px;background:var(--red);color:var(--white);font-family:"Roboto",sans-serif;font-size:15px;text-align:center;line-height:29px}
.dish-name{position:absolute;font-family:"Roboto",sans-serif;font-size:17px;color:var(--red)}
.dish-desc{position:absolute;width:272px;font-size:11px;line-height:21px;color:#555}

/* banquet */
.banquet{position:absolute;left:0;top:1264px;width:1200px;height:421px;background:linear-gradient(90deg,#2e2e2e 0%,#474543 35%,#3a3836 65%,#2c2c2c 100%)}
.banquet-tab{position:absolute;left:479px;top:1256px;width:242px;height:65px;background:var(--red);color:var(--white);font-family:"Roboto",sans-serif;font-size:28px;text-align:center;line-height:65px;box-shadow:0 3px 6px rgba(0,0,0,.35)}
.banquet-price{position:absolute;font-family:"Open Sans",sans-serif;font-size:35px;color:var(--white);font-weight:600}
.banquet-min{position:absolute;font-size:17px;font-weight:700;color:var(--white)}
.banquet-photo{position:absolute;top:1452px;width:207px;height:184px;border-bottom:4px solid var(--red)}
.course{position:absolute;width:178px;border:1px solid rgba(255,255,255,.8);background:rgba(0,0,0,.35);color:var(--white);font-family:"Roboto",sans-serif;font-size:13px;padding:10px 12px}
.course .head{display:flex;align-items:center;gap:10px;font-weight:500;text-transform:uppercase}
.course .tick{width:13px;height:13px;border-radius:50%;background:var(--white);display:flex;align-items:center;justify-content:center}
.course .items{margin:7px 0 0 35px;font-size:12px;line-height:22px;font-weight:500}

/* best dishes */
.arrow-btn{position:absolute;top:1727px;width:28px;height:28px;border-radius:50%;border:1.5px solid #555;display:flex;align-items:center;justify-content:center}
.best-card{position:absolute;top:1864px;width:272px;height:180px;background:#f6f6f6;box-shadow:0 6px 8px -4px rgba(0,0,0,.2)}
.best-card .basket{position:absolute;left:51px;top:20px;width:170px;height:150px;border-radius:50%;background:radial-gradient(circle,#b5452a 0%,#c87a3f 45%,#e3b878 60%,#f6f6f6 72%)}
.best-name{position:absolute;top:2058px;font-family:"Roboto",sans-serif;font-size:17px;color:#444}

/* footer */
.site-footer{position:absolute;left:0;top:2136px;width:1200px;height:235px;background:var(--footer);color:#bbb;font-size:12px}
.footer-col{position:absolute;top:26px}
.footer-col h4{font-family:"Roboto",sans-serif;font-weight:400;font-size:15px;color:var(--white);margin-bottom:18px;letter-spacing:.3px}
.footer-col p{line-height:21px}
.footer-col .label{color:var(--white);margin-top:8px}
.social{display:flex;align-items:center;gap:12px;margin-bottom:14px;font-size:11px}
.social span.dot{width:24px;height:24px;border-radius:50%;border:1.5px solid #888}
.newsletter{position:absolute;left:836px;top:0;width:192px;height:217px;background:var(--red);padding:26px 20px}
.newsletter h4{font-family:"Roboto",sans-serif;font-weight:400;font-size:15px;color:var(--white);margin-bottom:12px}
.newsletter .field{height:29px;background:var(--white);border-radius:2px;font-size:10px;color:#666;padding:8px;margin-bottom:10px}
.newsletter .btn{display:inline-block;border:1px solid var(--white);border-radius:4px;color:var(--white);font-size:11px;padding:5px 10px}
.footer-bar{position:absolute;left:0;top:2371px;width:1200px;height:55px;background:var(--footer-bar);color:#aaa;font-size:12px;text-align:center;line-height:55px}
</style>
</head>
<body>

<header class="site-header">
  <div class="contact-line" style="top:62px">Call Us : +08 8240 5176</div>
  <div class="contact-line" style="top:90px">info@chefwen.com.au</div>
  <div class="brand">
    <div class="brand-mark"></div>
    <div class="brand-name">Chef Wen Chinese Restaurant</div>
  </div>
  <div class="search">Search
    <svg width="12" height="12" viewBox="0 0 12 12"><circle cx="5" cy="5" r="3.6" fill="none" stroke="#aaa" stroke-width="1.3"/><line x1="7.6" y1="7.6" x2="11" y2="11" stroke="#aaa" stroke-width="1.3"/></svg>
  </div>
</header>

<div class="ribbon-tail left"></div>
<div class="ribbon-tail right"></div>
<nav class="main-nav">
  <a href="#">Home</a><a href="#">About us</a><a href="#">Our Menu</a><a href="#">Wine List</a><a href="#">Gallery</a><a href="#">Lumen Court</a><a href="#">Contact</a>
</nav>

<section class="hero" role="img" aria-label="Close-up photo of golden fried spring rolls on lettuce with red chilli and onion">
</section>
<div class="hero-text" style="top:362px;font-size:56px;font-weight:500">SPRING ROLLS</div>
<div class="hero-text" style="top:446px;font-size:38px;font-weight:400">(3 per serve)</div>
<div class="hero-text" style="top:500px;font-size:38px;font-weight:400">Price $6.8</div>
<div class="slider-dots"><span class="active"></span><span></span><span></span><span></span></div>
<div class="hero-shadow"></div>

<h2 class="section-title" style="top:741px;font-size:32px;font-weight:400">Welcome To Chef Wen Restaurant</h2>
<div class="divider" style="top:812px"></div>
<div class="divider-badge" style="top:794px">
  <svg width="16" height="16" viewBox="0 0 16 16"><circle cx="8" cy="6" r="4" fill="#333"/><rect x="4" y="11" width="8" height="3" fill="#333"/></svg>
</div>
<p class="intro">Chef Wen is named after its' executive chef, Mr. Wen. Chef Wen has been in his career for nearly two decades before he moved to Australia nine years ago. He settled in Adelaide then started his first restaurant, Lumen Court in Eastbrook. Lumen Court has been</p>

<div class="dish-photo" style="left:171px;top:931px;background:linear-gradient(135deg,#f4f4f4,#ef6a4c 40%,#e84a30 65%,#f7f7f7)" role="img" aria-label="Plate of salmon sashimi slices"></div>
<div class="dish-photo" style="left:464px;top:931px;background:linear-gradient(135deg,#fafafa,#f0a08a 40%,#e25a3c 65%,#f5efe6)" role="img" aria-label="Steamed whole coral trout with garnish"></div>
<div class="dish-photo" style="left:757px;top:931px;background:linear-gradient(135deg,#f6d9c8,#e2552f 45%,#d9b48a 75%,#efe3d2)" role="img" aria-label="Cooked red crab pieces"></div>
<div class="price-tag" style="left:171px;top:923px">$14.99</div>
<div class="price-tag" style="left:464px;top:923px">$14.99</div>
<div class="price-tag" style="left:757px;top:923px">$14.99</div>
<div class="dish-name" style="left:171px;top:1126px">Salmon Sashimi</div>
<div class="dish-name" style="left:464px;top:1126px">Steamed Whole Coral Trout</div>
<div class="dish-name" style="left:757px;top:1126px">Frozen Crab</div>
<p class="dish-desc" style="left:171px;top:1153px">Lorem ipsum dolor sit amet, consectetur ipiscing elit, sed do eiusmod tempor Lorem ipsum dolor sit amet, consectetur ipiscing elit.</p>
<p class="dish-desc" style="left:464px;top:1153px">Lorem ipsum dolor sit amet, consectetur ipiscing elit, sed do eiusmod tempor Lorem ipsum dolor sit amet, consectetur ipiscing elit.</p>
<p class="dish-desc" style="left:757px;top:1153px">Lorem ipsum dolor sit amet, consectetur ipiscing elit, sed do eiusmod tempor Lorem ipsum dolor sit amet, consectetur ipiscing elit.</p>

<section class="banquet" role="img" aria-label="Dark kitchen backdrop with a chef and scattered vegetables"></section>
<div class="banquet-tab">Banquet Menu</div>

<div class="banquet-price" style="left:171px;top:1353px">$33 PER PERSON</div>
<div class="banquet-min" style="left:171px;top:1404px">(minimum for 4-6 people)</div>
<div class="banquet-photo" style="left:171px;background:linear-gradient(150deg,#f4f1ea,#9aa36a 40%,#c9a86a 60%,#7a3a24 90%)" role="img" aria-label="Shallot pancake held with chopsticks"></div>
<div class="course" style="left:399px;top:1452px;height:97px">
  <div class="head"><span class="tick"><svg width="8" height="8" viewBox="0 0 8 8"><path d="M1 4l2 2 4-4" stroke="#333" stroke-width="1.5" fill="none"/></svg></span>Entrée</div>
  <div class="items">Spring Rolls<br>Shallot Pancake</div>
</div>
<div class="course" style="left:399px;top:1556px;height:38px"><div class="head"><span class="tick"><svg width="8" height="8" viewBox="0 0 8 8"><path d="M1 4l2 2 4-4" stroke="#333" stroke-width="1.5" fill="none"/></svg></span>Main Course</div></div>
<div class="course" style="left:399px;top:1599px;height:39px"><div class="head"><span class="tick"><svg width="8" height="8" viewBox="0 0 8 8"><path d="M1 4l2 2 4-4" stroke="#333" stroke-width="1.5" fill="none"/></svg></span>Dessert</div></div>

<div class="banquet-price" style="left:623px;top:1353px">$48 PER PERSON</div>
<div class="banquet-min" style="left:623px;top:1404px">(minimum for 8-10 people)</div>
<div class="banquet-photo" style="left:623px;background:linear-gradient(150deg,#efe9dc,#c98a4a 40%,#e6c67a 60%,#6a4a2a 90%)" role="img" aria-label="Noodle dish with dipping sauce"></div>
<div class="course" style="left:851px;top:1452px;height:97px">
  <div class="head"><span class="tick"><svg width="8" height="8" viewBox="0 0 8 8"><path d="M1 4l2 2 4-4" stroke="#333" stroke-width="1.5" fill="none"/></svg></span>Entrée</div>
  <div class="items">Shallot Pancake<br>Chicken Sweet Corn</div>
</div>
<div class="course" style="left:851px;top:1556px;height:38px"><div class="head"><span class="tick"><svg width="8" height="8" viewBox="0 0 8 8"><path d="M1 4l2 2 4-4" stroke="#333" stroke-width="1.5" fill="none"/></svg></span>Main Course</div></div>
<div class="course" style="left:851px;top:1599px;height:39px"><div class="head"><span class="tick"><svg width="8" height="8" viewBox="0 0 8 8"><path d="M1 4l2 2 4-4" stroke="#333" stroke-width="1.5" fill="none"/></svg></span>Dessert</div></div>

<div class="arrow-btn" style="left:172px"><svg width="10" height="10" viewBox="0 0 10 10"><path d="M6.5 2L3.5 5l3 3" stroke="#444" stroke-width="1.5" fill="none"/></svg></div>
<h2 class="section-title" style="top:1723px;font-size:26px;font-weight:400;text-transform:uppercase">Dishes The Best Of Chef Wen</h2>
<div class="arrow-btn" style="left:1001px"><svg width="10" height="10" viewBox="0 0 10 10"><path d="M3.5 2l3 3-3 3" stroke="#444" stroke-width="1.5" fill="none"/></svg></div>
<div class="divider" style="top:1798px"></div>
<div class="divider-badge" style="top:1780px">
  <svg width="14" height="14" viewBox="0 0 14 14"><path d="M2 2l10 10M12 2L2 12" stroke="#d50d0d" stroke-width="2"/></svg>
</div>

<div class="best-card" style="left:171px"><div class="basket" role="img" aria-label="Steamed pork ribs in a bamboo basket"></div></div>
<div class="best-card" style="left:464px"><div class="basket" role="img" aria-label="Shanghai pork buns in a bamboo basket" style="background:radial-gradient(circle,#efe4c4 0%,#e7d3a4 45%,#d9ae6c 60%,#f6f6f6 72%)"></div></div>
<div class="best-card" style="left:757px"><div class="basket" role="img" aria-label="Spicy ox tripe in a bamboo basket" style="background:radial-gradient(circle,#c8321e 0%,#d65a33 45%,#e3b878 60%,#f6f6f6 72%)"></div></div>
<div class="price-tag" style="left:171px;top:1856px">$14.99</div>
<div class="price-tag" style="left:464px;top:1856px">$14.99</div>
<div class="price-tag" style="left:757px;top:1856px">$14.99</div>
<div class="best-name" style="left:171px">Steamed Pork Ribs</div>
<div class="best-name" style="left:464px">Shanghai Pork Buns</div>
<div class="best-name" style="left:757px">Spicy Ox Tripe</div>

<footer class="site-footer">
  <div class="footer-col" style="left:171px">
    <h4>TRADING HOURS</h4>
    <p>We are open 7 days</p>
    <p class="label">LUNCH</p>
    <p>Monday to Friday 11:30am - 2:30pm</p>
    <p>Saturday to Sunday 11:00am - 3:00pm</p>
    <p class="label">DINNER</p>
    <p>Monday to Sunday 6:00pm Until Late</p>
  </div>
  <div class="footer-col" style="left:438px">
    <h4>GET IN TOUCH</h4>
    <p>4/218 Kestrel Road<br>Hallow Park, SA, 5071</p>
    <p style="margin-top:16px">Toll free: &nbsp;08 9417 3052</p>
    <p style="margin-top:16px">info@chefwen.com.au</p>
  </div>
  <div class="footer-col" style="left:650px">
    <h4>FOLLOW US</h4>
    <div class="social"><span class="dot"></span>Join Us On Fanpage</div>
    <div class="social"><span class="dot"></span>Join Us On Chirper</div>
    <div class="social"><span class="dot"></span>Join Us On Vidtube</div>
  </div>
  <div class="newsletter">
    <h4>NEWSLETTER</h4>
    <div class="field">Enter Your Name</div>
    <div class="field">Enter Your Email</div>
    <span class="btn">subscribe</span>
  </div>
</footer>
<div class="footer-bar">© 2014 - Chef Wen Chinese Restaurant</div>

</body>
</html>
```